Slow Winter Song. A CD of beautiful 17th century music for lute played by a world famous lutenist.

Hi designers,
My name is Ollie Pellicott and I am an international lute player in need of a CD cover design. I am blind, so will be relying on other people's eyes and descriptions during the process, including yours! Are you up for the challenge?
My CD is called Slow Winter Song. It's beautiful lute music from the 17th century, very intimate and carming, but also very powerful.
I would like you to use the attached image, and find a way to include the following text in a tasteful way:
The text for the front cover is as follows:
Slow Winter Song
Oliver Pellicott - lute and theorbo
Music by Harcrane, Fennimore, Brackley, Tarn, Cavallenti and Ruhlendorf.
Here is a viewora link to some of the music I play, which should give you an idea:
www.viewora.net/olliepellicott1
Here is a link to my website, where you can see the covers of my other CDs, and get more information about me:
www.oliverpellicott.net
I'm excited to receive your design and ideas.
Best wishes
Ollie

```html
<!DOCTYPE html>
<html lang="en">
<head>
<meta charset="utf-8">
<title>Slow Winter Song – CD Cover</title>
<link rel="stylesheet" href="https://fonts.googleapis.com/css2?family=Sancreek&family=Michroma&family=Mrs+Saint+Delafield&display=swap">
<style>
  :root {
    --bg-light: #c9c5bc;
    --bg-mid: #a7a399;
    --bg-dark: #6f6b63;
    --cream: #ece8de;
    --cream-band: rgba(236, 232, 222, 0.72);
    --frame-grey: #6a6863;
    --title-red: #8e1b21;
    --ink: #1d1c1a;
    --lute-light: #f1eee6;
    --lute-shade: #bdb8ad;
  }
  * { box-sizing: border-box; margin: 0; padding: 0; }
  html, body { width: 1200px; height: 1200px; overflow: hidden; }
  body { background: var(--bg-mid); }

  .cover {
    position: relative;
    width: 1200px;
    height: 1200px;
    overflow: hidden;
    background: radial-gradient(ellipse at 50% 35%, var(--bg-light) 0%, var(--bg-mid) 55%, var(--bg-dark) 100%);
  }
  .cover__backdrop {
    position: absolute;
    inset: 0;
    background: linear-gradient(to bottom, rgba(255,255,255,0.05) 0%, rgba(255,255,255,0) 60%, rgba(40,38,34,0.35) 100%);
  }
  .cover__ground {
    position: absolute;
    left: 0; right: 0; bottom: 0;
    height: 100px;
    background: linear-gradient(to bottom, #7d796f, #4e4b45);
  }

  .lute-illustration {
    position: absolute;
    left: 26px;
    top: 70px;
    width: 370px;
    height: 1005px;
    border-radius: 40px 40px 185px 185px;
    background: linear-gradient(100deg, var(--lute-shade) 0%, var(--lute-light) 45%, var(--lute-shade) 100%);
    z-index: 3;
  }

  .title-label {
    position: absolute;
    left: 431px;
    top: 40px;
    width: 560px;
    height: 813px;
    z-index: 2;
  }
  .title-label svg { position: absolute; inset: 0; }
  .title-label__text {
    position: absolute;
    inset: 0;
    text-align: center;
    color: var(--title-red);
    font-family: "Sancreek", serif;
    font-weight: 400;
    text-transform: uppercase;
  }
  .title-label__line {
    position: absolute;
    display: block;
    left: 50px; right: 50px;
    line-height: 1;
    white-space: nowrap;
    font-size: 112px;
    letter-spacing: 1px;
  }
  .title-label__line::first-letter { font-size: 1.25em; }
  .title-label__line--1 { top: 115px; }
  .title-label__line--2 { top: 300px; }
  .title-label__line--3 { top: 485px; }
  .title-label__subtitle {
    position: absolute;
    left: 0; right: 0;
    top: 680px;
    font-family: "Mrs Saint Delafield", cursive;
    color: var(--ink);
    font-size: 40px;
    line-height: 0.95;
    text-transform: none;
    letter-spacing: 0;
  }

  .credit-band {
    position: absolute;
    left: 0; right: 0;
    top: 895px;
    height: 205px;
    background: var(--cream-band);
    z-index: 1;
  }
  .credit-band__rule {
    position: absolute;
    left: 0; right: 0;
    height: 10px;
    border-top: 2px solid var(--frame-grey);
    border-bottom: 2px solid var(--frame-grey);
  }
  .credit-band__rule--top { top: 0; }
  .credit-band__rule--bottom { bottom: 0; }

  .credits {
    position: absolute;
    left: 400px;
    right: 0;
    top: 912px;
    text-align: center;
    font-family: "Michroma", sans-serif;
    color: var(--ink);
    text-transform: uppercase;
    z-index: 2;
  }
  .credits__artist { font-size: 25px; letter-spacing: 2px; line-height: 36px; }
  .credits__instruments { font-size: 25px; letter-spacing: 2px; line-height: 36px; }
  .credits__music-by { margin-top: 18px; font-size: 19px; letter-spacing: 1px; line-height: 26px; }
  .credits__composers { font-size: 19px; letter-spacing: 1px; line-height: 26px; }
</style>
</head>
<body>
<main class="cover">
  <div class="cover__backdrop" role="img" aria-label="Faded grey damask pattern over a misty wintry landscape with trees"></div>
  <div class="cover__ground"></div>

  <div class="credit-band">
    <div class="credit-band__rule credit-band__rule--top"></div>
    <div class="credit-band__rule credit-band__rule--bottom"></div>
  </div>

  <div class="lute-illustration" role="img" aria-label="Engraved illustration of a pale lute with rose soundhole and bent-back pegbox"></div>

  <div class="title-label">
    <svg viewBox="0 0 560 813" width="560" height="813" aria-hidden="true">
      <path d="M0,95 L32,95 L32,62 Q280,-18 528,62 L528,95 L560,95 L560,718 L528,718 L528,751 Q280,831 32,751 L32,718 L0,718 Z"
            fill="var(--frame-grey)"/>
      <path d="M8,102 L40,102 L40,69 Q280,-6 520,69 L520,102 L552,102 L552,711 L520,711 L520,744 Q280,819 40,744 L40,711 L8,711 Z"
            fill="var(--cream)"/>
      <path d="M18,110 L48,110 L48,76 Q280,5 512,76 L512,110 L542,110 L542,703 L512,703 L512,737 Q280,808 48,737 L48,703 L18,703 Z"
            fill="none" stroke="var(--frame-grey)" stroke-width="2"/>
    </svg>
    <div class="title-label__text">
      <h1>
        <span class="title-label__line title-label__line--1">Slow</span>
        <span class="title-label__line title-label__line--2">Winter</span>
        <span class="title-label__line title-label__line--3">Song</span>
      </h1>
      <p class="title-label__subtitle">17th century<br>music for lute</p>
    </div>
  </div>

  <section class="credits">
    <p class="credits__artist">Oliver Pellicott</p>
    <p class="credits__instruments">Lute and Theorbo</p>
    <p class="credits__music-by">Music by:</p>
    <p class="credits__composers">Harcrane • Fennimore • Brackley</p>
    <p class="credits__composers">Tarn • Cavallenti • Ruhlendorf</p>
  </section>
</main>
</body>
</html>
```